Stationery Design Project for Nimbora, Chicago

Nimbora, a street parking application which helps car drivers find a street parking spot by offering an ideal path along which to look for parking. This path is calculated by our algorithm based on data (e.g. historical data, baseball games schedule, etc.). Along this path the driver will find a spot and will also save 70% of the search time. Customer we target is reg. between 21 and 45 yo.

We envision something young, fresh, bright and original. Slightly abstract maybe. It should represent the idea and elements of finding street parking in the city, e.g. car(s), parking spot, people, city, etc. (just ideas!).

Logo is attached.

Requirement:
- Business Cards (2 Sided Full Color CMYK)
- Letterhead (1 Sided Full Color CMYK)
- Envelope (1 Sided Full Color CMYK)
- Sticker (1 Sided Full Color CMYK), round with a 2inch diameter.

Reason: We're starting to get more and more designs and need more time to look into all of them. Very exciting!! Thanks to everybody!

Hi all, we're in the process of selecting our favs. Though choices!!! Really good submissions. Will keep you posted and sorry for the delay.

Target Market(s)

Car drivers and owners between 21 and 45

Industry/Entity Type

Parking

Requirements
Must have
• Sticker should be round and include company URL nimbora.com and the new logo which we will attach soon.
Should not have
• Should not be too serious or boring.

```html
<!DOCTYPE html>
<html lang="en">
<head>
<meta charset="utf-8">
<title>Nimbora Business Cards</title>
<link rel="stylesheet" href="https://fonts.googleapis.com/css2?family=Source+Sans+3:wght@400;600;700&display=swap">
<style>
  :root {
    --backdrop: #d6d6d6;
    --card: #ffffff;
    --ink: #1c1c1c;
    --brand-blue: #1b5fc4;
    --band-blue-dark: #1a2f9a;
    --band-blue-light: #2a6fd6;
    --band-grey: #5c5c60;
    --wordmark: #222222;
  }
  * { margin: 0; padding: 0; box-sizing: border-box; }
  html, body {
    width: 954px; height: 1200px; overflow: hidden;
    background: var(--backdrop);
    font-family: "Source Sans 3", "Myriad Pro", Arial, sans-serif;
    color: var(--ink);
  }
  .sheet { position: relative; width: 954px; height: 1200px; }
  .card {
    position: absolute; left: 74px; width: 796px; height: 454px;
    background: var(--card); border-radius: 30px; overflow: hidden;
  }
  .card--front { top: 133px; }
  .card--back { top: 651px; }
  .brand { position: absolute; display: flex; align-items: center; }
  .brand__dot { border-radius: 50%; background: var(--brand-blue); flex: none; }
  .brand__name {
    font-weight: 600; color: var(--wordmark); line-height: 1;
    letter-spacing: 1px;
  }
  .card--front .brand { left: 48px; top: 39px; }
  .card--front .brand__dot { width: 154px; height: 154px; margin-right: 26px; }
  .card--front .brand__name { font-size: 96px; }
  .card--back .brand { left: 48px; top: 61px; }
  .card--back .brand__dot { width: 190px; height: 190px; margin-right: 40px; }
  .card--back .brand__name { font-size: 124px; }

  .name-band {
    position: absolute; left: 512px; top: 219px; width: 284px; height: 78px;
    display: flex;
  }
  .name-band__main {
    width: 240px; padding: 6px 0 0 18px; color: #fff;
    background: radial-gradient(ellipse at 75% 40%, var(--band-blue-light), var(--band-blue-dark) 75%);
  }
  .name-band__tab { flex: 1; background: var(--band-grey); }
  .person__name { font-size: 25px; font-weight: 700; line-height: 1.2; }
  .person__role { font-size: 19px; font-weight: 700; line-height: 1.2; }

  .contact { position: absolute; font-size: 19px; line-height: 1; }
  .contact li { list-style: none; white-space: nowrap; }
  .contact b { font-weight: 700; }
  .card--front .contact { left: 533px; top: 318px; }
  .card--front .contact li:nth-child(1) { margin-bottom: 13px; }
  .card--front .contact li:nth-child(2) { margin-bottom: 11px; }
  .card--front .contact li:nth-child(3) { margin-bottom: 7px; }
  .card--back .contact { left: 533px; top: 380px; }
  .card--back .contact li:nth-child(1) { margin-bottom: 7px; }

  .address {
    position: absolute; left: 49px; top: 376px;
    font-size: 19px; line-height: 26px; font-style: normal;
  }
</style>
</head>
<body>
<main class="sheet">
  <section class="card card--front" aria-label="Business card front">
    <div class="brand">
      <span class="brand__dot"></span>
      <span class="brand__name">nimbora</span>
    </div>
    <div class="name-band">
      <div class="name-band__main">
        <p class="person__name">Your Name</p>
        <p class="person__role">Designation</p>
      </div>
      <div class="name-band__tab"></div>
    </div>
    <ul class="contact">
      <li><b>t</b> : 123-456-7890</li>
      <li><b>m</b> : 123-456-7890</li>
      <li><b>e</b> : name@website.com</li>
      <li><b>w</b> : www.website.com</li>
    </ul>
    <address class="address">City Name, Street Name<br>State Name, Country Code</address>
  </section>

  <section class="card card--back" aria-label="Business card back">
    <div class="brand">
      <span class="brand__dot"></span>
      <span class="brand__name">nimbora</span>
    </div>
    <ul class="contact">
      <li><b>e</b> : name@website.com</li>
      <li><b>w</b> : www.website.com</li>
    </ul>
  </section>
</main>
</body>
</html>
```